Powerpoint, Graphics for Sermon Series

I am starting a sermon series on the short letters if Scripture that are between Hebrews and Revelation. The sermon series will be called "Walking Unmarked Trails: Lasting Lessons from Quiet Hills."

Think about finding a packet of letters in an Attic. There is only the dialogue of the writer. We don't know exactly what the receivers were going through or even what their response to the letters were/are!

Target Market(s)

Local Church

Industry/Entity Type

Christian

Font styles to use
Serif
Sans Serif

Colors

Designer to choose colors to be used in the design.

Requirements
Must have
• Powerpoint Slide with Title -
• Background Slide -
• It would be great to have both JPG, PNG, and Photoshop/Indesign that can be used for powerpoint, both in 4x3 ration and wide... Need Title Slide with typography and background slide for text to go over the top of.
• Stick with the theme -- Walking Unmarked Trails
• I am including our church logo, but don't feel like you need to use it in anyway.
Nice to have
• Social Media Slides - Square Slide, Facebook Header
• Greyscale Version?

```html
<!DOCTYPE html>
<html lang="en">
<head>
<meta charset="utf-8">
<title>Sermon Series Content Slide</title>
<link rel="stylesheet" href="https://fonts.googleapis.com/css2?family=Cinzel:wght@700&family=Lato:wght@400;700&display=swap">
<style>
  :root {
    --title-brown: #66391c;
    --accent-amber: #c97d10;
    --body-grey: #3c3c3c;
    --band-brown: #7b5034;
    --paper: #ffffff;
    --photo-dark: #2e1f12;
    --photo-mid: #6a4526;
    --photo-light: #c9b497;
  }
  html, body {
    margin: 0;
    padding: 0;
    width: 1200px;
    height: 900px;
    overflow: hidden;
    background: var(--paper);
  }
  .slide {
    position: relative;
    width: 1200px;
    height: 900px;
    background: var(--paper);
    overflow: hidden;
  }
  .slide-title {
    position: absolute;
    left: 44px;
    top: 30px;
    margin: 0;
    font-family: "Cinzel", "Trajan Pro", serif;
    font-weight: 700;
    font-size: 50px;
    letter-spacing: 0.5px;
    color: var(--title-brown);
  }
  .church-name {
    position: absolute;
    right: 24px;
    top: 52px;
    display: flex;
    align-items: center;
    gap: 12px;
    font-family: "Lato", sans-serif;
    font-weight: 700;
    font-size: 26px;
    color: var(--title-brown);
  }
  .church-name .mark {
    width: 18px;
    height: 18px;
    background: var(--title-brown);
  }
  .content {
    position: absolute;
    left: 52px;
    top: 220px;
    width: 560px;
  }
  .subtitle {
    margin: 0 0 4px;
    font-family: "Lato", sans-serif;
    font-weight: 700;
    font-size: 33px;
    color: var(--accent-amber);
  }
  .body-copy {
    margin: 0;
    font-family: "Lato", sans-serif;
    font-weight: 400;
    font-size: 21.5px;
    line-height: 38px;
    color: var(--body-grey);
    hyphens: auto;
  }
  .feature-photo {
    position: absolute;
    left: 683px;
    top: 258px;
    width: 517px;
    height: 464px;
    background:
      radial-gradient(ellipse at 60% 60%, var(--photo-light) 0%, rgba(201,180,151,0.6) 28%, rgba(106,69,38,0) 60%),
      linear-gradient(180deg, var(--photo-dark) 0%, var(--photo-mid) 70%, #4a2f18 100%);
  }
  .footer-band {
    position: absolute;
    left: 0;
    bottom: 0;
    width: 1200px;
    height: 26px;
    background: var(--band-brown);
  }
</style>
</head>
<body>
  <main class="slide">
    <h1 class="slide-title">SLIDE TITLE HERE</h1>

    <div class="church-name">
      <span class="mark"></span>
      <span>Cedar Ridge Fellowship</span>
    </div>

    <section class="content">
      <h2 class="subtitle">Subtext title here</h2>
      <p class="body-copy">Lorem Ipsum is simply dummy text of the printing and typesetting industry. Lorem Ipsum has been the industry's standard dummy text ever since the 1500s, when an unknown printer took a galley of type and scrambled it to make a type specimen book. It has survived not only five centuries, but also the leap into electronic typesetting, remaining essentially unchanged. It was popularised in the 1960s with the release of Lettermark sheets containing Lorem Ipsum passages, and more recently with desktop publishing software like Folio PageSetter including versions of Lorem Ipsum. It has survived not only five centuries, but also the leap into electronic typesetting, remaining essentially unchanged. It was popularised in the 1960s with the release of Lettermark sheets containing Lorem</p>
    </section>

    <div class="feature-photo" role="img" aria-label="A stack of old letters tied with twine on a wooden table beside a red wax seal stamp"></div>

    <div class="footer-band"></div>
  </main>
</body>
</html>
```